Redesign current business card for food company

i would like to redesign my business card. our company is food company, our product range from chips, juices, milk and etc (mostly dried food stuff).
I want o keep same logo but , the rest is open to new design.
you can check at our website about our company www.orvelpantry.com

Target Market(s)

most of food company

Industry/Entity Type

Business

Contact Information for Business Card

I want to keep more to blue color...

Colors
3176b5
abd036

Requirements
Must have
• our old logo
Nice to have
• we do not mind to have nice material on bus card in order to accomplish nice design. for example: using spot uv, embossed and etc.

```html
<!DOCTYPE html>
<html lang="en">
<head>
<meta charset="utf-8">
<title>Orvel Business Card</title>
<link rel="stylesheet" href="https://fonts.googleapis.com/css2?family=Open+Sans:wght@400;600;700&display=swap">
<style>
  :root {
    --page-bg: #e9e7e4;
    --card-dark: #1b1c1e;
    --card-dark-edge: #25272a;
    --brand-blue: #3176b5;
    --brand-blue-light: #2f8fd6;
    --brand-blue-deep: #1f5fa8;
    --text-light: #e6e8ea;
    --text-white: #ffffff;
    --divider: #3a3d41;
  }
  * { box-sizing: border-box; margin: 0; padding: 0; }
  html, body {
    width: 1200px; height: 844px; overflow: hidden;
    background: var(--page-bg);
    font-family: "Open Sans", Arial, sans-serif;
  }
  .stage {
    position: relative; width: 1200px; height: 844px;
    display: flex; align-items: center; justify-content: center; gap: 60px;
  }
  .card {
    width: 520px; height: 298px; border-radius: 4px;
    position: relative; overflow: hidden;
    box-shadow: 0 6px 18px rgba(0,0,0,.18);
  }
  .card-front {
    background: linear-gradient(135deg, var(--card-dark-edge), var(--card-dark));
  }
  .card-back {
    background: linear-gradient(160deg, var(--brand-blue-light), var(--brand-blue-deep));
    display: flex; align-items: center; justify-content: center;
  }
  .brand-name {
    font-weight: 600; line-height: 1; white-space: nowrap;
  }
  .card-front .brand-name {
    position: absolute; left: 40px; top: 122px;
    font-size: 56px; color: var(--text-light);
  }
  .card-back .brand-name { font-size: 60px; color: var(--text-white); }
  .contact {
    position: absolute; left: 278px; right: 16px; top: 48px; bottom: 40px;
    padding-left: 18px; border-left: 1px solid var(--divider);
    color: var(--text-light); font-size: 13px;
  }
  .contact-name { color: var(--brand-blue-light); font-weight: 700; font-size: 15px; }
  .contact-role { font-size: 13px; margin-bottom: 12px; }
  .contact-list { list-style: none; }
  .contact-list li { display: flex; align-items: center; gap: 8px; line-height: 20px; white-space: nowrap; }
  .contact-list svg { width: 11px; height: 11px; fill: var(--text-light); flex: none; }
  .contact-address { margin-top: 14px; white-space: nowrap; }
</style>
</head>
<body>
<main class="stage">
  <section class="card card-front" aria-label="Business card front">
    <p class="brand-name">orvel</p>
    <div class="contact">
      <p class="contact-name">Daniel Mahardika</p>
      <p class="contact-role">President</p>
      <ul class="contact-list">
        <li><svg viewBox="0 0 12 12"><path d="M2 1h2l1 3-1.5 1a7 7 0 0 0 3.5 3.5L8 7l3 1v2a1 1 0 0 1-1 1A9 9 0 0 1 1 2a1 1 0 0 1 1-1z"/></svg>555 014 2288</li>
        <li><svg viewBox="0 0 12 12"><path d="M3 1h6v3H3zM1 5h10v5H9V8H3v2H1zM3 9h6v3H3z"/></svg>555 014 2277</li>
        <li><svg viewBox="0 0 12 12"><path d="M3.5 0h5a1 1 0 0 1 1 1v10a1 1 0 0 1-1 1h-5a1 1 0 0 1-1-1V1a1 1 0 0 1 1-1zM4 1.5v8h4v-8z"/></svg>555 018 4637</li>
        <li><svg viewBox="0 0 12 12"><path d="M0 2h12v1L6 7 0 3zM0 4.5l6 4 6-4V10H0z"/></svg>daniel@orvelpantry.com</li>
        <li><svg viewBox="0 0 12 12"><path d="M6 0a6 6 0 1 0 0 12A6 6 0 0 0 6 0zm0 1.2a4.8 4.8 0 0 1 0 9.6 4.8 4.8 0 0 1 0-9.6zM5.3 2v8h1.4V2zM2 5.3v1.4h8V5.3z"/></svg>www.orvelpantry.com</li>
      </ul>
      <p class="contact-address">418 W Linden Ave. Alder CA 91234</p>
    </div>
  </section>
  <section class="card card-back" aria-label="Business card back">
    <p class="brand-name">orvel</p>
  </section>
</main>
</body>
</html>
```